Harborline Auto LLC

Car Dealer Customer Service
Address: 2874 Cresthaven Road, Shelbyville, TN 37162
web: www.harborlineautoxq.net
email: harborlineautoxq@mailnest.example
Phone: (931) 555-0148
Phone: (629) 555-0173

```html
<!DOCTYPE html>
<html lang="en">
<head>
<meta charset="utf-8">
<title>Harborline Auto LLC – Business Card</title>
<link rel="stylesheet" href="https://fonts.googleapis.com/css2?family=Montserrat:wght@400;500;800&display=swap">
<style>
  :root {
    --brand-blue: #2a8fcb;
    --brand-blue-deep: #1f74ad;
    --brand-gold: #ecb43e;
    --ink: #1c1c1c;
    --card: #ffffff;
    --backdrop: #e9eaec;
  }
  * { margin: 0; padding: 0; box-sizing: border-box; }
  html, body {
    width: 1200px; height: 900px; overflow: hidden;
    background: var(--backdrop);
    font-family: "Montserrat", sans-serif;
  }
  .canvas {
    width: 1200px; height: 900px;
    display: flex; flex-direction: column;
    align-items: center; justify-content: center; gap: 34px;
  }
  .card {
    position: relative;
    width: 700px; height: 400px;
    background: var(--card);
    box-shadow: 0 6px 18px rgba(0,0,0,0.12);
    overflow: hidden;
  }
  .brand {
    position: absolute;
    display: flex; align-items: center; gap: 16px;
    white-space: nowrap;
  }
  .brand-dot {
    width: 46px; height: 46px; border-radius: 50%;
    background: var(--brand-blue-deep);
    flex: none;
  }
  .brand-name {
    font-weight: 800;
    font-size: 36px;
    letter-spacing: 1px;
    color: var(--brand-blue-deep);
    text-transform: uppercase;
    line-height: 1;
    white-space: nowrap;
  }
  .card-front .brand {
    left: 50%; top: 50%;
    transform: translate(-50%, -50%);
  }
  .card-back .brand {
    left: 30px; top: 178px;
    gap: 12px;
  }
  .card-back .brand-name { font-size: 22px; letter-spacing: 0.5px; }
  .card-back .brand-dot { width: 30px; height: 30px; }
  .divider {
    position: absolute;
    left: 358px; top: 52px;
    width: 2px; height: 200px;
    background: var(--brand-blue);
  }
  .contact {
    position: absolute;
    left: 376px; top: 52px;
    font-size: 14px; line-height: 23px;
    color: var(--ink);
    list-style: none;
  }
  .contact .role { font-weight: 500; }
  .contact li { display: flex; align-items: center; gap: 8px; white-space: nowrap; }
  .contact svg { width: 12px; height: 12px; flex: none; fill: var(--brand-blue); }
  .contact .web-domain { color: var(--brand-blue); }
  .bands {
    position: absolute; left: 0; bottom: 0;
    width: 700px; height: 90px;
  }
</style>
</head>
<body>
<main class="canvas">

  <section class="card card-front" aria-label="Business card front">
    <div class="brand">
      <span class="brand-dot"></span>
      <span class="brand-name">Harborline Auto</span>
    </div>
  </section>

  <section class="card card-back" aria-label="Business card back">
    <div class="brand">
      <span class="brand-dot"></span>
      <span class="brand-name">Harborline Auto</span>
    </div>

    <div class="divider"></div>

    <ul class="contact">
      <li class="role">Car Dealer Customer Service</li>
      <li>2874 Cresthaven Road,</li>
      <li>Shelbyville, TN 37162</li>
      <li>
        <svg viewBox="0 0 16 16" aria-hidden="true"><path d="M3.6 1.5l2.3 2.6-1.2 1.8c.9 2 2.4 3.5 4.4 4.4l1.8-1.2 2.6 2.3-1.2 2.3C7.6 13.5 2.5 8.4 1.3 3z"/></svg>
        (931) 555-0148
      </li>
      <li>
        <svg viewBox="0 0 16 16" aria-hidden="true"><path d="M1 5c2-3 12-3 14 0l-1 2-3-1V4.5H5V6L2 7z"/><rect x="3" y="8" width="10" height="6" rx="1"/></svg>
        (629) 555-0173
      </li>
      <li>
        <svg viewBox="0 0 16 16" aria-hidden="true"><path d="M1 3h14v1.2L8 9 1 4.2z"/><path d="M1 5.8l7 4.8 7-4.8V13H1z"/></svg>
        harborlineautoxq@mailnest.example
      </li>
      <li>
        <svg viewBox="0 0 16 16" aria-hidden="true"><circle cx="8" cy="8" r="7"/></svg>
        <span>www.<span class="web-domain">harborlineautoxq.net</span></span>
      </li>
    </ul>

    <svg class="bands" viewBox="0 0 700 90" aria-hidden="true">
      <rect x="0" y="51" width="178" height="9" fill="var(--brand-gold)"/>
      <rect x="186" y="51" width="150" height="9" fill="var(--brand-blue)"/>
      <rect x="344" y="51" width="152" height="9" fill="var(--brand-gold)"/>
      <polygon points="0,66 506,66 506,20 526,4 700,4 700,90 0,90" fill="var(--brand-blue)"/>
    </svg>
  </section>

</main>
</body>
</html>
```